Goodlooking website for a company who is working in the IT consultancy

We want a new website designed in WordPress. You can take www.vantoro.nl as an example. It should be a website with some short blocks of information about the company, nice pictures of our partners and our employees. A job page with a clear filter.

Target Market(s)

B2B

Industry/Entity Type

It Company

Coding

Coded - Design and coding required

Number of Pages Required

5+ page

Font styles to use
Sans Serif

Colors
0455a3
34a7d8

Requirements
Must have
• Check briefing

```html
<!DOCTYPE html>
<html lang="nl">
<head>
<meta charset="utf-8">
<title>Vantoro – Critical IT Systems</title>
<link href="https://fonts.googleapis.com/css2?family=Poppins:wght@400;500&family=Open+Sans:wght@400;600&family=Roboto+Condensed:wght@400;700&display=swap" rel="stylesheet">
<style>
:root{
  --blue:#0455a3;
  --sky:#34a7d8;
  --teal:#1a8a78;
  --ink:#1c1c1c;
  --dark:#111418;
  --muted:#555;
  --line:#d8d8d8;
  --white:#fff;
  --partner-red:#3a3a3a;
  --partner-grey:#e2e2e2;
  --partner-dock:#3a8fc8;
}
*{margin:0;padding:0;box-sizing:border-box}
html,body{width:1200px;height:3871px;overflow:hidden}
body{position:relative;background:var(--white);font-family:"Open Sans",sans-serif;color:var(--ink)}
.abs{position:absolute}
.center{left:0;width:1200px;text-align:center}
.h2{font-family:"Poppins",sans-serif;font-weight:500;font-size:36px;color:var(--ink)}
.sub{font-family:"Poppins",sans-serif;font-size:21px;color:#222}

/* header */
.brand{display:flex;align-items:center;gap:14px}
.brand-dot{width:58px;height:58px;border-radius:50%;background:var(--blue)}
.brand-name{font-family:"Poppins",sans-serif;font-weight:500;font-size:34px;letter-spacing:2px;color:#222}
.nav a{position:absolute;top:50px;font-family:"Poppins",sans-serif;font-size:19px;color:#222;text-decoration:none}
.login{left:1022px;top:46px;width:88px;height:34px;background:var(--blue);color:#fff;border-radius:3px;font-family:"Poppins",sans-serif;font-size:18px;text-align:center;line-height:34px}

/* hero */
.hero-photo{left:0;top:120px;width:1200px;height:585px;background:linear-gradient(100deg,#5c6d7d 0%,#2c3b4a 35%,#1a2633 65%,#101821 100%)}
.hero-title{right:120px;top:338px;text-align:right;color:#fff;font-family:"Roboto Condensed",sans-serif}
.hero-title .t1{font-weight:700;font-size:51px;letter-spacing:.5px}
.hero-title .t2{font-size:44px;margin-top:-4px}
.dots span{position:absolute;left:1157px;width:8px;height:8px;border-radius:50%;background:#fff}

/* services */
.service{width:250px;text-align:center}
.service .ring{width:114px;height:114px;border-radius:50%;border:2px solid var(--sky);margin:0 auto;display:flex;align-items:center;justify-content:center}
.service h3{font-family:"Poppins",sans-serif;font-weight:400;font-size:18px;margin-top:24px;line-height:24px;height:48px;display:flex;align-items:center;justify-content:center}
.service p{font-size:14px;line-height:22px;color:#444;margin-top:2px}
.service .chev{margin-top:6px}

/* about */
.about-text{left:140px;width:920px;top:1505px;text-align:center;color:#fff;font-size:15.5px;line-height:28px}
.btn-white{background:#fff;color:#222;border-radius:22px;font-size:16px;text-align:center}

/* jobs */
.jobs{left:163px;top:2056px;width:872px;border-top:3px solid #bbb}
.job{position:relative;height:114px;border:1px solid var(--line);box-shadow:0 1px 4px rgba(0,0,0,.15);margin-top:2px;background:#fff}
.job .title{position:absolute;left:55px;font-size:15px;color:#222}
.job .meta{position:absolute;left:55px;font-size:12px;color:var(--blue);display:flex;align-items:center;gap:4px}
.job .meta.time{color:#222}
.job .cell{position:absolute;top:50%;transform:translateY(-50%);font-size:15px;color:#222}
.job .apply{position:absolute;left:717px;top:50%;transform:translateY(-50%);width:98px;height:36px;background:var(--teal);color:#fff;font-size:14px;text-align:center;line-height:36px;border-radius:2px}
.more{top:2448px;font-size:15px;color:var(--blue)}

/* contact */
.contact-photo{left:0;top:2542px;width:1200px;height:529px;background:linear-gradient(180deg,#15191d 0%,#1f262c 55%,#2c3135 100%)}
.field{border:1.5px solid #cfcfcf;border-radius:3px;color:#fff;font-size:16px;padding-left:16px;display:flex;align-items:center}

/* partners */
.partner{border-radius:3px}

/* footer */
.social span{position:absolute;top:3578px;width:24px;height:24px;border-radius:3px;background:#8a8a8a}
.flinks a{position:absolute;top:3799px;font-family:"Poppins",sans-serif;font-size:15px;color:#fff;text-decoration:none}
</style>
</head>
<body>

<header>
  <div class="abs brand" style="left:90px;top:30px">
    <div class="brand-dot"></div>
    <div class="brand-name">VANTORO</div>
  </div>
  <nav class="nav">
    <a style="left:508px">Home</a>
    <a style="left:609px">solutions</a>
    <a style="left:733px">Team</a>
    <a style="left:826px">Job</a>
    <a style="left:898px">Contact</a>
  </nav>
  <div class="abs login">Login</div>
</header>

<section>
  <div class="abs hero-photo" role="img" aria-label="Two IT engineers with a laptop in a server room"></div>
  <svg class="abs" style="left:0;top:600px" width="1200" height="110" viewBox="0 0 1200 110">
    <polygon points="500,70 1200,20 1200,110 500,110" fill="var(--teal)"/>
    <polygon points="0,110 0,105 1200,85 1200,110" fill="#fff"/>
    <polygon points="0,110 500,70 560,110" fill="#fff"/>
  </svg>
  <div class="abs hero-title">
    <div class="t1">CRITICAL IT SYSTEMS</div>
    <div class="t2">Cloud Consultancy</div>
  </div>
  <div class="dots">
    <span style="top:346px"></span><span style="top:370px"></span><span style="top:394px"></span><span style="top:418px"></span>
  </div>
</section>

<section>
  <div class="abs center h2" style="top:812px">What we do</div>
  <div class="abs center sub" style="top:861px">Neque porro quisquam est dolorem</div>

  <div class="abs service" style="left:84px;top:947px">
    <div class="ring"><svg width="52" height="44" viewBox="0 0 52 44"><rect x="8" y="4" width="36" height="26" rx="2" fill="none" stroke="var(--sky)" stroke-width="4"/><rect x="2" y="33" width="48" height="6" rx="2" fill="var(--sky)"/></svg></div>
    <h3>Automation &amp; Deployment</h3>
    <p>Wij verzorgen het volledig<br>Design en implementatie</p>
    <svg class="chev" width="16" height="16" viewBox="0 0 16 16"><path d="M2 2l6 5 6-5M2 8l6 5 6-5" fill="none" stroke="#222" stroke-width="2"/></svg>
  </div>
  <div class="abs service" style="left:347px;top:947px">
    <div class="ring"><svg width="46" height="46" viewBox="0 0 46 46"><path d="M40 6c-12 0-20 8-25 18l7 7c10-5 18-13 18-25z" fill="var(--sky)"/><path d="M14 25l-8 2 6-10h8zM21 32l-2 8 10-6v-8z" fill="var(--sky)"/><path d="M11 31l-5 9 9-5z" fill="var(--sky)"/></svg></div>
    <h3>Mission Critical Solutions</h3>
    <p>Line by line code review<br>-Functionality testing</p>
    <svg class="chev" width="16" height="16" viewBox="0 0 16 16"><path d="M2 2l6 5 6-5M2 8l6 5 6-5" fill="none" stroke="#222" stroke-width="2"/></svg>
  </div>
  <div class="abs service" style="left:608px;top:947px">
    <div class="ring"><svg width="56" height="38" viewBox="0 0 56 38"><path d="M14 36a12 12 0 0 1-2-24 15 15 0 0 1 28-4 12 12 0 0 1 4 28z" fill="var(--sky)"/></svg></div>
    <h3>Cloud Consultancy</h3>
    <p>Kestrel Advisory have a thor-<br>ough understanding</p>
    <svg class="chev" width="16" height="16" viewBox="0 0 16 16"><path d="M2 2l6 5 6-5M2 8l6 5 6-5" fill="none" stroke="#222" stroke-width="2"/></svg>
  </div>
  <div class="abs service" style="left:871px;top:947px">
    <div class="ring"><svg width="46" height="46" viewBox="0 0 46 46" fill="var(--sky)"><rect x="2" y="2" width="12" height="12"/><rect x="17" y="2" width="12" height="12"/><rect x="32" y="2" width="12" height="12"/><rect x="2" y="17" width="12" height="12"/><rect x="17" y="17" width="12" height="12"/><rect x="32" y="17" width="12" height="12"/><rect x="2" y="32" width="12" height="12"/><rect x="17" y="32" width="12" height="12"/><rect x="32" y="32" width="12" height="12"/></svg></div>
    <h3>Hyperconverged<br>Infrastructures</h3>
    <p>Help you build your technical<br>team&nbsp; Advice on ERC</p>
    <svg class="chev" width="16" height="16" viewBox="0 0 16 16"><path d="M2 2l6 5 6-5M2 8l6 5 6-5" fill="none" stroke="#222" stroke-width="2"/></svg>
  </div>
</section>

<section>
  <svg class="abs" style="left:0;top:1311px" width="1200" height="540" viewBox="0 0 1200 540">
    <defs>
      <linearGradient id="aboutBlue" x1="0" y1="0" x2="1" y2="0">
        <stop offset="0" stop-color="#0a5fa3"/><stop offset=".5" stop-color="#1a78b8"/><stop offset="1" stop-color="#0f64a8"/>
      </linearGradient>
    </defs>
    <polygon points="0,0 560,80 1200,40 1200,440 0,540" fill="#121212"/>
    <polygon points="0,40 1200,95 1200,440 0,480" fill="url(#aboutBlue)"/>
  </svg>
  <div class="abs center h2" style="top:1444px;color:#fff">About us</div>
  <p class="abs about-text">Vantoro levert diensten die er voor zorg dragen dat uw "automatisering" wordt geautomatiseerd. Binnen IT omgevingen vinden veelal repeterende taken plaats die onnodig veel tijd in beslag nemen en ook nog eens foutgevoelig zijn. Een komma vergeten of een commando niet uitvoeren kan grote gevolgen hebben voor de dienstverlening. Het automatiseren van deze taken zorgt ervoor dat u altijd een betrouwbaar proces afspeelt met bekende uitkomsten. Het geeft het interne team ook meer tijd om zich te richten op innovaties, nieuwe technieken of verbeteringen binnen uw eigen dienstverlening.</p>
  <div class="abs btn-white" style="left:529px;top:1677px;width:140px;height:42px;line-height:42px">Read More</div>
</section>

<section>
  <div class="abs center h2" style="top:1926px">Job Listing</div>
  <div class="abs center sub" style="top:1976px">Neque porro quisquam est qui dolorem</div>
  <div class="abs jobs">
    <div class="job">
      <div class="title" style="top:17px">Seles&amp; Marketing Coordinator</div>
      <div class="meta" style="top:45px"><svg width="9" height="12" viewBox="0 0 9 12"><path d="M4.5 0a4.5 4.5 0 0 1 4.5 4.5C9 8 4.5 12 4.5 12S0 8 0 4.5A4.5 4.5 0 0 1 4.5 0z" fill="var(--blue)"/></svg>Germany, Hanover</div>
      <div class="meta time" style="top:70px"><svg width="11" height="11" viewBox="0 0 11 11"><circle cx="5.5" cy="5.5" r="4.5" fill="none" stroke="#222" stroke-width="1.5"/><path d="M5.5 3v3h2" fill="none" stroke="#222" stroke-width="1.2"/></svg>65 days 21:46:59</div>
      <div class="cell" style="left:383px">£27500</div>
      <div class="cell" style="left:550px">Full time</div>
      <div class="apply">Apply Now</div>
    </div>
    <div class="job">
      <div class="title" style="top:17px">ENGINEERING TECHNICIAN</div>
      <div class="meta" style="top:45px"><svg width="9" height="12" viewBox="0 0 9 12"><path d="M4.5 0a4.5 4.5 0 0 1 4.5 4.5C9 8 4.5 12 4.5 12S0 8 0 4.5A4.5 4.5 0 0 1 4.5 0z" fill="var(--blue)"/></svg>Netherlands, Rotterdam</div>
      <div class="meta time" style="top:70px"><svg width="11" height="11" viewBox="0 0 11 11"><circle cx="5.5" cy="5.5" r="4.5" fill="none" stroke="#222" stroke-width="1.5"/><path d="M5.5 3v3h2" fill="none" stroke="#222" stroke-width="1.2"/></svg>42 days 20:41:55</div>
      <div class="cell" style="left:383px">£27500</div>
      <div class="cell" style="left:550px">Full time</div>
      <div class="apply">Apply Now</div>
    </div>
    <div class="job">
      <div class="title" style="top:35px">SCIENCE TEACHER</div>
      <div class="meta" style="top:63px"><svg width="9" height="12" viewBox="0 0 9 12"><path d="M4.5 0a4.5 4.5 0 0 1 4.5 4.5C9 8 4.5 12 4.5 12S0 8 0 4.5A4.5 4.5 0 0 1 4.5 0z" fill="var(--blue)"/></svg>England, London, Camden</div>
      <div class="cell" style="left:383px">£27500</div>
      <div class="cell" style="left:550px">Full time</div>
      <div class="apply">Apply Now</div>
    </div>
  </div>
  <div class="abs center more">View More <svg width="16" height="10" viewBox="0 0 16 10"><path d="M0 5h13M9 1l4 4-4 4" fill="none" stroke="var(--blue)" stroke-width="2"/></svg></div>
</section>

<section>
  <div class="abs contact-photo" role="img" aria-label="City skyline at dusk"></div>
  <svg class="abs" style="left:0;top:2542px" width="1200" height="100" viewBox="0 0 1200 100">
    <polygon points="0,0 1200,0 1200,30 0,70" fill="#fff"/>
    <polygon points="620,50 1200,0 1200,90" fill="var(--teal)"/>
  </svg>
  <svg class="abs" style="left:0;top:2980px" width="1200" height="92" viewBox="0 0 1200 92">
    <polygon points="0,10 680,50 0,92" fill="var(--teal)"/>
    <polygon points="0,92 1200,40 1200,92" fill="#fff"/>
  </svg>
  <div class="abs center h2" style="top:2673px;color:#fff">Contact us</div>
  <div class="abs field" style="left:217px;top:2766px;width:245px;height:52px">Name</div>
  <div class="abs field" style="left:477px;top:2766px;width:245px;height:52px">Phone</div>
  <div class="abs field" style="left:738px;top:2766px;width:243px;height:52px">Email id</div>
  <div class="abs field" style="left:217px;top:2846px;width:764px;height:54px">Comment</div>
  <div class="abs btn-white" style="left:867px;top:2923px;width:114px;height:39px;line-height:39px">Submit</div>
</section>

<section>
  <div class="abs center h2" style="top:3163px">Partnerships</div>
  <div class="abs center sub" style="top:3210px">Neque porro quisquam est qui dolorem</div>
  <div class="abs partner" style="left:253px;top:3304px;width:127px;height:72px;background:var(--partner-red)" role="img" aria-label="Partner badge"></div>
  <div class="abs partner" style="left:441px;top:3308px;width:132px;height:67px;background:var(--blue)" role="img" aria-label="Partner badge"></div>
  <div class="abs partner" style="left:630px;top:3322px;width:142px;height:38px;background:var(--partner-grey)" role="img" aria-label="Partner badge"></div>
  <div class="abs partner" style="left:828px;top:3294px;width:119px;height:98px;border-radius:50%;background:var(--partner-dock)" role="img" aria-label="Partner badge"></div>
</section>

<footer>
  <svg class="abs" style="left:0;top:3515px" width="1200" height="356" viewBox="0 0 1200 356">
    <polygon points="0,5 560,80 0,100" fill="var(--blue)"/>
    <polygon points="0,95 1200,40 1200,356 0,356" fill="var(--dark)"/>
  </svg>
  <div class="social">
    <span style="left:966px"></span><span style="left:1003px"></span><span style="left:1040px"></span><span style="left:1077px"></span>
  </div>
  <div class="abs brand" style="left:90px;top:3681px">
    <div class="brand-dot" style="width:50px;height:50px;background:#fff"></div>
    <div class="brand-name" style="color:#fff;font-size:30px">VANTORO</div>
  </div>
  <div class="abs" style="left:614px;top:3695px;font-family:'Poppins',sans-serif;font-size:16px;color:#fff">JOIN OUR NEWSLETTER</div>
  <div class="abs" style="left:828px;top:3680px;width:282px;height:52px;border:1.5px solid #ddd;border-radius:26px;color:#ccc;font-size:14px;padding-left:24px;line-height:49px">Email address
    <svg style="position:absolute;right:18px;top:16px" width="18" height="18" viewBox="0 0 18 18"><circle cx="9" cy="9" r="9" fill="#ddd"/><path d="M9 4v10M4 9h10" stroke="var(--dark)" stroke-width="2"/></svg>
  </div>
  <div class="abs" style="left:85px;top:3772px;width:1025px;height:1px;background:#444"></div>
  <nav class="flinks">
    <a style="left:85px">Home</a><a style="left:158px">solutions</a><a style="left:251px">Team</a><a style="left:317px">Job</a><a style="left:364px">Contact</a>
  </nav>
  <div class="abs" style="right:90px;top:3801px;font-size:13px;color:#fff">Copyright © 2018, All Rights Reserved</div>
</footer>

</body>
</html>
```